Tandem Hearth Works Pty Ltd

We need business cards for a company based in Perth, we install, service and maintain fire equipment.
On the front we want a great design with our logo and a small spot for our full company name, general company email address and office number. On the back we need space for our name, title, mobile number and email address on the back.

Target Market(s)

Facility managers and commercial/industrial building owners/occupiers.

Contact Information for Business Card

Font styles to use
Sans Serif

Requirements
Must have
• Please only submit 5 of your best samples.
Darker tones are preferred.
Nice to have
• We want to use, black, red and grey. Keep it modern and clean.
I've attached the company logo and a sample of a boarder we use on our emergency plans.
Should not have
• No preference. Let the designer choose.

```html
<!DOCTYPE html>
<html lang="en">
<head>
<meta charset="utf-8">
<title>Tandem Hearth Works – Business Cards</title>
<link rel="stylesheet" href="https://fonts.googleapis.com/css2?family=Arimo:wght@400;700&display=swap">
<style>
  :root {
    --page-bg: #0b0b0b;
    --card-bg: #1a1a1a;
    --brand-red: #e31b23;
    --text-light: #e6e6e6;
    --text-grey: #b3b3b3;
    --divider: #6a6a6a;
  }
  * { margin: 0; padding: 0; box-sizing: border-box; }
  html, body {
    width: 1200px; height: 900px; overflow: hidden;
    background: var(--page-bg);
    font-family: "Arimo", Arial, sans-serif;
  }
  .sheet {
    width: 1200px; height: 900px;
    display: flex; flex-direction: column; align-items: center; justify-content: center;
    gap: 40px;
  }
  .card {
    width: 620px; height: 354px;
    background: var(--card-bg);
    display: flex; align-items: center;
    padding: 0 40px 0 56px;
    box-shadow: 0 10px 30px rgba(0,0,0,.6);
  }
  .brand {
    width: 220px;
    color: var(--brand-red);
    font-weight: 700;
    font-size: 30px;
    line-height: 1.1;
    text-transform: uppercase;
    letter-spacing: .5px;
  }
  .divider {
    width: 1px; height: 140px;
    background: var(--divider);
    margin: 0 30px 0 24px;
    transform: skewX(-14deg);
  }
  .details { flex: 1; }
  .company-name, .person-name {
    color: var(--brand-red);
    font-weight: 700;
    text-transform: uppercase;
    font-size: 17px;
    line-height: 1.15;
    letter-spacing: .6px;
  }
  .office-phone {
    color: var(--text-light);
    font-weight: 700;
    font-size: 22px;
    margin: 6px 0 6px;
  }
  .person-title {
    color: var(--text-grey);
    font-size: 15px;
    margin: 2px 0 12px;
  }
  .contact-line {
    display: flex; align-items: center; gap: 10px;
    color: var(--text-light);
    font-size: 14px;
    line-height: 1.55;
  }
  .contact-line svg { width: 15px; height: 15px; flex: none; }
</style>
</head>
<body>
<main class="sheet">
  <section class="card card-front">
    <div class="brand">Tandem Hearth Works</div>
    <div class="divider"></div>
    <div class="details">
      <p class="company-name">Tandem Hearth Works<br>Pty Ltd</p>
      <p class="office-phone">08 5550 1920</p>
      <p class="contact-line">
        <svg viewBox="0 0 16 16" aria-hidden="true"><rect x="1" y="3" width="14" height="10" fill="var(--brand-red)"/><path d="M1 3l7 6 7-6" fill="none" stroke="var(--card-bg)" stroke-width="1.4"/></svg>
        info@tandemhearth.com
      </p>
      <p class="contact-line">
        <svg viewBox="0 0 16 16" aria-hidden="true"><g fill="none" stroke="var(--brand-red)" stroke-width="1.4"><circle cx="8" cy="8" r="6.3"/><ellipse cx="8" cy="8" rx="2.8" ry="6.3"/><path d="M1.7 8h12.6M2.8 4.8h10.4M2.8 11.2h10.4"/></g></svg>
        www.tandemhearth.com
      </p>
    </div>
  </section>

  <section class="card card-back">
    <div class="brand">Tandem Hearth Works</div>
    <div class="divider"></div>
    <div class="details">
      <p class="person-name">Marcus Delaney</p>
      <p class="person-title">Managing Director</p>
      <p class="contact-line">
        <svg viewBox="0 0 16 16" aria-hidden="true"><rect x="4" y="1" width="8" height="14" rx="1.5" fill="none" stroke="var(--brand-red)" stroke-width="1.5"/><circle cx="8" cy="12.4" r=".9" fill="var(--brand-red)"/></svg>
        0412 555 274
      </p>
      <p class="contact-line">
        <svg viewBox="0 0 16 16" aria-hidden="true"><rect x="1" y="3" width="14" height="10" fill="var(--brand-red)"/><path d="M1 3l7 6 7-6" fill="none" stroke="var(--card-bg)" stroke-width="1.4"/></svg>
        marcus@tandemhearth.com
      </p>
    </div>
  </section>
</main>
</body>
</html>
```